Business Card for my New Brokerage

Looking to get a business card design for my new Real Estate Brokerage.
I want it with Picture, Phone Number, Email, Website, Office Address
Name and Designation. Please add logo too.

Target Market(s)

Real Estate Investors or Home Buyers

Industry/Entity Type

Real Estate

Contact Information for Business Card

Name, Email, Phone Number, website, email, office address

Colors
EB3D1F
EC4F4E
F09395
F8D3D4
FCEDEE

Requirements
Must have
• Minimalistic, Clean, Modern, Photo
Nice to have
• White and Red Colors

```html
<!DOCTYPE html>
<html lang="en">
<head>
<meta charset="utf-8">
<title>Ember Realty Inc — Business Card</title>
<link href="https://fonts.googleapis.com/css2?family=Montserrat:wght@500;700;800&display=swap" rel="stylesheet">
<style>
  :root {
    --brand-red: #e3392a;
    --ink: #2b2b2b;
    --card: #ffffff;
    --backdrop: #c9cccd;
    --photo-light: #f3ebe4;
    --photo-mid: #b48a72;
    --photo-dark: #6b4636;
  }
  * { margin: 0; padding: 0; box-sizing: border-box; }
  html, body {
    width: 1187px; height: 1200px; overflow: hidden;
    background: var(--backdrop);
    font-family: "Montserrat", sans-serif;
  }
  .card {
    position: absolute;
    background: var(--card);
    border-radius: 16px;
    overflow: hidden;
  }
  .card--front { left: 219px; top: 122px; width: 751px; height: 429px; }
  .card--back  { left: 214px; top: 644px; width: 760px; height: 434px; }

  .brand-name {
    position: absolute;
    color: var(--brand-red);
    font-weight: 700;
    line-height: 1;
    white-space: nowrap;
  }
  .card--front .brand-name {
    left: 0; right: 0; top: 186px;
    text-align: center;
    font-size: 56px;
  }
  .card--back .brand-name {
    left: 51px; top: 76px;
    font-size: 34px;
  }

  .agent { position: absolute; left: 51px; top: 196px; color: var(--ink); }
  .agent__name { font-size: 23px; font-weight: 800; color: var(--brand-red); letter-spacing: 0.02em; }
  .agent__role { font-size: 17px; font-weight: 500; margin-top: 4px; letter-spacing: 0.03em; }
  .rule { width: 58px; height: 3px; background: var(--brand-red); margin: 5px 0 9px; }
  .address { font-size: 17px; font-weight: 500; letter-spacing: 0.03em; line-height: 28px; }
  .contact { list-style: none; margin-top: 4px; }
  .contact li { display: flex; align-items: center; gap: 8px; font-size: 17px; font-weight: 500; letter-spacing: 0.04em; height: 29px; }
  .contact svg { width: 14px; height: 14px; fill: var(--brand-red); flex: none; }

  .portrait {
    position: absolute; left: 410px; top: 27px; width: 350px; height: 407px;
    background: linear-gradient(to bottom, var(--photo-dark) 0%, var(--photo-mid) 40%, var(--photo-light) 62%, var(--photo-light) 100%);
    border-top-left-radius: 45% 28%;
    border-top-right-radius: 45% 28%;
  }
</style>
</head>
<body>
  <section class="card card--front">
    <p class="brand-name">Ember Realty Inc</p>
  </section>

  <section class="card card--back">
    <p class="brand-name">Ember Realty Inc</p>

    <div class="agent">
      <h1 class="agent__name">LAURA BENNETT</h1>
      <p class="agent__role">Broker Associate</p>
      <div class="rule"></div>
      <p class="address">210 Harbor Point Suite<br>Westfield Business Park</p>
      <div class="rule"></div>
      <ul class="contact">
        <li><svg viewBox="0 0 24 24"><path d="M6.6 10.8a15.1 15.1 0 0 0 6.6 6.6l2.2-2.2a1 1 0 0 1 1-.25 11.4 11.4 0 0 0 3.6.57 1 1 0 0 1 1 1V20a1 1 0 0 1-1 1A17 17 0 0 1 3 4a1 1 0 0 1 1-1h3.5a1 1 0 0 1 1 1c0 1.25.2 2.45.57 3.57a1 1 0 0 1-.25 1z"/></svg>555-014-2287</li>
        <li><svg viewBox="0 0 24 24"><path d="M2 5h20v14H2z"/><path d="M3 6l9 7 9-7" fill="none" stroke="#fff" stroke-width="1.6"/></svg>hello@emberrealtyinc.com</li>
        <li><svg viewBox="0 0 24 24"><circle cx="12" cy="12" r="10"/><path d="M2 12h20M12 2c3 3 3 17 0 20M12 2c-3 3-3 17 0 20M4 7h16M4 17h16" fill="none" stroke="#fff" stroke-width="1.3"/></svg>www.emberrealtyinc.com</li>
      </ul>
    </div>

    <div class="portrait" role="img" aria-label="Portrait photo of the broker associate"></div>
  </section>
</body>
</html>
```